Bold, Modern, Clean "Kestrelwaymassage.com" website

Why we stand out?
We are a male and female mobile massage team. Our names are Paul and Lina. 
Kestrel Way is a Seattle based mobile massage service. Our massage is offered to the community with a goal of facilitating balance within each individual. We specialize in integrated Pain management, and sports/medical massage therapy. Every client's first assessment is attended by our male and female massage therapist team. Depending on the goals identified for an individual determines which therapist will be assigned to provide treatment, if not both.

Our passion...
Here at Kestrel Way, we have a great passion for Postural Resoration and how it is integrated into an individual's Massage treatment. We pride ourselves in being natural facilitators of healing, which takes the ego of the therapist out of the client's healing process. We strive to deliver the best massage possible by including modalities such as Neuromuscular, Myofascial release, spontaneous muscle release, postural restoration, orthopedic, and medical massage.

Our education...

We are both Graduates of Venmora, school of massage therapy. We have continuing education in medical massage, myofacial release, trigger point therapy, postural restoration, anatomy, and spontaneous muscle release. Lina is also a Certified Yoga Instructor, which amplifies her experience with flexibility and strength as it pertains to each individual. Paul's passion is Massage, stretching, and strength training to encourage postural restoration and realignment.

Our rates-

Our rates are $75/ 60 minutes, $95/ 90 minutes, and $120/ 120 minutes.

Education-
Both Lina and I worked as behavioral health professionals that specialized in life skills mentoring for youth who had experienced different types of trauma. This led us both to want to help others in a different environment, where individuals can be empowered to take responsibility over their own healing. To us, massage is a type of manipulation physical therapy, that encourages healing on many levels.

Advice to any massage client-
The most important thing to 'us', as Licenced providers is to get you on to our table to show you our skills. But a good therapist never forgets that it's not about what we do for you, but what we can facilitate for you. Your health and healing has nothing to do with us. It is yours, not ours. Identify what your goals are with any Therapist, and know what the end looks like. Progress should be tangible, such as range of motion, and decreased pain.

Lina and Paul at Kestrel Way are awesome! I recently had open heart surgery, and Lina worked on me to increase my range of motion while helping with the pinched nerve from my arm being in the same position for so long during my surgery. My wife drives a lot for work, and Paul has helped decrease her neck and lower back pain immensely. They are seriously the best therapists I have ever worked with. I would recommend them to anyone who needs anything from stress relief to a medical massage treatment. They are professional, up beat, easy going, and always on time. And, I love that they meet us where ever we like! We did a staycation recently, where they came to our hotel to give us relaxation massages. Although usually they come to our home, where we focus on pain related issues. We will continue to work with them for a long, long time.

Target Market(s)

Mobile massage therapy clients

Industry/Entity Type

Massage Therapy

Coding

Coded - Design and coding required

Number of Pages Required

1 page

Font styles to use
Serif
Sans Serif

Requirements
Must have
• Please add or remove any information that would help the presentation of our website. Our logo is posted below, please include into the website.
• Please include a contact field that includes, kestrelwaymassage@fernmail.net,
• (206) 555-0148
• We have also included our own stock photos, as well as a photo of Paul and Lina. Please include a cropped photo of both massage therapists.

```html
<!DOCTYPE html>
<html lang="en">
<head>
<meta charset="utf-8">
<title>Kestrel Way Mobile Massage</title>
<link href="https://fonts.googleapis.com/css2?family=Open+Sans:ital,wght@0,400;0,600;0,700;1,400&display=swap" rel="stylesheet">
<style>
:root{
  --navy:#23275e;
  --navy-deep:#1c2052;
  --nav:#262a66;
  --cyan:#17b3d6;
  --ink:#23275e;
  --body:#2b2b2b;
  --band-a:#9b6bb5;
  --band-b:#c58ac0;
  --white:#ffffff;
  --ring:#b478c2;
}
*{box-sizing:border-box;margin:0;padding:0}
html,body{width:1200px;height:1200px;overflow:hidden}
body{font-family:"Open Sans",Arial,sans-serif;background:var(--white);position:relative;color:var(--body)}
.abs{position:absolute;white-space:nowrap}

/* header */
.site-header{position:absolute;left:0;top:0;width:1200px;height:114px;background:linear-gradient(180deg,#24285f,#2a2e6b)}
.brand{position:absolute;left:250px;top:16px;display:flex;align-items:center;gap:16px}
.brand-dot{width:80px;height:80px;border-radius:50%;background:var(--cyan);border:3px solid var(--white)}
.brand-name{color:var(--white);font-weight:700;font-size:34px;line-height:34px;letter-spacing:1px;width:140px}
.hours{left:528px;top:22px;color:var(--white);font-size:10px;line-height:12px;display:flex;align-items:center;gap:4px}
.join{left:654px;top:21px;color:var(--cyan);font-size:10.5px;line-height:14px}
.join b{font-weight:600}
.socials{left:769px;top:11px;display:flex;gap:3px}
.socials span{width:37px;height:37px;border-radius:50%;background:var(--cyan);display:block}
.contact{display:flex;gap:8px;align-items:center}
.contact .icon{width:26px;height:26px;border:1px solid var(--cyan);display:flex;align-items:center;justify-content:center}
.contact p{color:var(--white);font-size:12px;line-height:13px}
.contact p small{color:var(--cyan);font-size:9px;font-weight:600}
.contact.phone{left:528px;top:64px}
.contact.post{left:763px;top:64px}
.contact.post p{font-size:10px}
.contact.post p small{font-weight:400}

/* nav */
.main-nav{position:absolute;left:0;top:114px;width:1200px;height:42px;background:var(--nav);border-top:1px solid #3a3f80}
.main-nav ul{list-style:none;display:flex;position:absolute;left:253px;top:0}
.main-nav li{color:var(--white);font-size:13.5px;height:42px;line-height:40px;padding:0 11px;border-right:1px solid #1e2255}
.main-nav li:last-child{border-right:0}
.main-nav li.active{border-bottom:3px solid var(--cyan)}

/* hero */
.hero{position:absolute;left:0;top:156px;width:1200px;height:381px;background:radial-gradient(ellipse at 35% 15%,#ffe9a8 0%,#f7a34a 25%,#d8502e 55%,#7a1e2a 100%)}
.hero-figure{position:absolute;left:660px;top:30px;width:260px;height:351px;background:linear-gradient(180deg,#5a1418,#2a0a0e);border-radius:120px 120px 0 0;opacity:.55}
.hero-copy{position:absolute;left:246px;top:180px;color:var(--navy)}
.hero-copy .kicker{font-weight:700;font-size:26px;line-height:26px}
.hero-copy h1{font-weight:700;font-size:32px;line-height:36px}
.hero-copy p{color:var(--white);font-size:20px;line-height:25px}
.hero-copy p em{font-style:italic}
.btn-outline{position:absolute;border:2px solid var(--cyan);color:var(--cyan);display:flex;align-items:center;justify-content:center;font-size:11px;white-space:nowrap}
.hero .btn-outline{left:246px;top:319px;width:170px;height:34px;background:rgba(255,255,255,.05);font-size:10.5px;font-weight:600;color:#1fc3e6}

/* band */
.band{position:absolute;left:0;top:537px;width:1200px;height:94px;background:linear-gradient(90deg,var(--band-a),var(--band-b) 55%,var(--band-a))}
.band p{position:absolute;right:610px;top:12px;text-align:right;color:var(--white);font-size:12px;line-height:13.5px;white-space:nowrap}
.band .btn-outline{left:610px;top:32px;width:211px;height:31px;border-color:var(--white);color:var(--white);font-size:13px;letter-spacing:2.5px}

/* welcome */
.section-title{position:absolute;left:0;width:1200px;text-align:center;font-size:17px}
.section-title b{font-weight:700}
.rule{position:absolute;left:475px;width:250px;height:1px;background:#dcdcdc}
.rule i{position:absolute;left:91px;top:-1px;width:68px;height:3px;background:var(--cyan)}
.welcome-title{top:672px;color:var(--ink)}
.welcome-rule{top:703px}
.photo{position:absolute}
.photo-left{left:234px;top:741px;width:188px;height:197px;background:linear-gradient(160deg,#b9b3a8,#6d6a8a 55%,#2b3d8f)}
.photo-right{left:734px;top:741px;width:232px;height:197px;background:linear-gradient(135deg,#c0466e,#e3a39a 55%,#b56a5a)}
.availability{position:absolute;left:734px;top:899px;width:152px;height:39px;background:var(--navy);clip-path:polygon(0 0,86% 0,100% 100%,0 100%);color:var(--white);padding:3px 6px}
.availability strong{display:block;font-size:13px;line-height:14px}
.availability span{font-size:11.5px;line-height:13px;white-space:nowrap}
.intro{position:absolute;left:441px;top:739px;width:276px}
.intro h2{font-weight:400;font-size:14px;line-height:17px;color:var(--ink);margin-bottom:10px}
.intro p{font-size:8.3px;line-height:12.4px;color:var(--body);margin-bottom:12px}
.intro .btn-outline{position:static;width:81px;height:31px;font-weight:700;font-size:8.5px;margin-top:8px}

/* treatments */
.treatments{position:absolute;left:0;top:984px;width:1200px;height:216px;background:linear-gradient(90deg,#45427f,#5b5596 50%,#4a4684)}
.treatments .section-title{top:40px;color:var(--white)}
.treat-rule{top:72px;background:rgba(255,255,255,.35)}
.treat-rule i{background:var(--white)}
.arrow{position:absolute;top:46px;width:28px;height:28px}
.circle{position:absolute;top:108px;width:180px;height:180px;border-radius:50%;border:3px solid var(--ring)}
</style>
</head>
<body>

<header class="site-header">
  <div class="brand"><span class="brand-dot"></span><span class="brand-name">KESTREL WAY</span></div>
  <div class="abs hours">
    <svg width="9" height="9" viewBox="0 0 10 10"><circle cx="5" cy="5" r="4" fill="none" stroke="#17b3d6"/><path d="M5 2.5V5h2" stroke="#17b3d6" fill="none"/></svg>
    Mon - Sat: 8:00 - 18:00
  </div>
  <div class="abs join">Join the <b>Conversation</b></div>
  <div class="abs socials" aria-label="Social links"><span></span><span></span><span></span><span></span><span></span></div>
  <div class="abs contact phone">
    <span class="icon"><svg width="12" height="12" viewBox="0 0 24 24"><path d="M6.6 10.8a15 15 0 006.6 6.6l2.2-2.2c.3-.3.7-.4 1-.2 1.1.4 2.3.6 3.6.6.6 0 1 .4 1 1V20c0 .6-.4 1-1 1A17 17 0 013 4c0-.6.4-1 1-1h3.5c.6 0 1 .4 1 1 0 1.3.2 2.5.6 3.6.1.3 0 .7-.2 1z" fill="#17b3d6"/></svg></span>
    <p>206.555.0148<br><small>kestrelwaymassage@fernmail.net</small></p>
  </div>
  <div class="abs contact post">
    <span class="icon"><svg width="13" height="13" viewBox="0 0 24 24"><path d="M3 11l9-8 9 8M5 9v11h14V9" fill="none" stroke="#17b3d6" stroke-width="2"/></svg></span>
    <p>Space for postal address of Kestrel Way<br><small>Country will b placed here.</small></p>
  </div>
</header>

<nav class="main-nav">
  <ul>
    <li class="active">Home</li><li>About Us</li><li>Passion</li><li>Education</li><li>Treatments</li><li>Advice</li><li>Packages</li><li>Testimonials</li><li>Contact Us</li>
  </ul>
</nav>

<section class="hero" role="img" aria-label="Woman meditating on a mountain top at sunset">
  <div class="hero-figure"></div>
  <div class="hero-copy">
    <div class="kicker">FIND</div>
    <h1>YOUR BALANCE.</h1>
    <p>For fitness and wellbeing.<br>Healing body, <em>mind and spirit!</em></p>
  </div>
  <div class="btn-outline">VIEW KESTREL WAY DETAILS</div>
</section>

<section class="band">
  <p>A tranquil experience, through caring hands.<br>Change the way you feel.<br>Come in stressed. Leave revitalized.<br>Dedicated to your health and wellbeing.<br>Essential Balance. <b>Massage &amp; Wellness.</b></p>
  <div class="btn-outline">VIEW OUR TREATMENTS</div>
</section>

<h2 class="section-title welcome-title" style="font-weight:400">Welcome to <b>Kestrel Way Mobile Massage</b></h2>
<div class="rule welcome-rule"><i></i></div>

<div class="photo photo-left" role="img" aria-label="Therapist sitting on a patterned floor"></div>
<div class="intro">
  <h2>The perfect place for some well-deserved pampering and relaxation.</h2>
  <p>Lorem ipsum dolor sit amet, consectetur adipisicing elit, sed do eiusmod tempor incididunt ut labore et dolore magna aliqua. Ut enim ad minim veniam, quis nostrud exercitation ullamco laboris nisi ut aliquip ex ea commodo consequat.</p>
  <p>Duis aute irure dolor in reprehenderit in voluptate velit esse cillum dolore eu fugiat nulla pariatur. Excepteur sint occaecat cupidatat non proident, sunt in culpa qui officia deserunt mollit anim id est laborum.</p>
  <div class="btn-outline">READ MORE</div>
</div>
<div class="photo photo-right" role="img" aria-label="Client relaxing during a back massage among flower petals"></div>
<div class="availability"><strong>Availability Check</strong><span>For your best Treatment</span></div>

<section class="treatments" role="group" aria-label="Treatments">
  <h2 class="section-title" style="font-weight:400">Still Water's <b>Treatments</b></h2>
  <div class="rule treat-rule"><i></i></div>
  <svg class="arrow" style="left:234px" viewBox="0 0 28 28"><circle cx="14" cy="14" r="13" fill="none" stroke="#fff" stroke-width="1.5"/><path d="M16 8l-6 6 6 6" fill="none" stroke="#fff" stroke-width="1.5"/></svg>
  <svg class="arrow" style="left:937px" viewBox="0 0 28 28"><circle cx="14" cy="14" r="13" fill="none" stroke="#fff" stroke-width="1.5"/><path d="M12 8l6 6-6 6" fill="none" stroke="#fff" stroke-width="1.5"/></svg>
  <div class="circle" style="left:274px;background:linear-gradient(160deg,#7a5a44,#c89a7a)" role="img" aria-label="Hot stone back treatment"></div>
  <div class="circle" style="left:510px;background:linear-gradient(160deg,#a8825e,#e3c2a4)" role="img" aria-label="Facial relaxation treatment"></div>
  <div class="circle" style="left:745px;background:linear-gradient(160deg,#6f8a3a,#b6c86a)" role="img" aria-label="Outdoor yoga and wellness session"></div>
</section>

</body>
</html>
```